Create a new business card

I’m looking to update my business card to make it match the rest of my brand. I will include my current website as well as what my vehicle designs look like, etc..
What my business currently services
Weekly maintenance pool openings / closings
Equipment repair, including pumps, heaters, salt systems, filters, etc.
We install automatic covers and maintain them as well as provide preventative maintenance

I would like to include my name.
Dorian Pelkin.
My title
Owner
My email
Dorian@tidewellnx.com
4015827160
Www.tidewellnx.com

```html
<!DOCTYPE html>
<html lang="en">
<head>
<meta charset="utf-8">
<title>Tidewell Pool Service – Business Card</title>
<link rel="stylesheet" href="https://fonts.googleapis.com/css2?family=Oswald:wght@400;500;600&display=swap">
<style>
  :root{
    --navy:#1f2d66;
    --navy-deep:#1a2658;
    --sky:#22b0e6;
    --orange:#e8682a;
    --white:#ffffff;
    --stage:#1d1d1f;
  }
  *{margin:0;padding:0;box-sizing:border-box}
  html,body{width:1200px;height:1122px;overflow:hidden;background:var(--stage)}
  body{font-family:"Oswald",sans-serif;position:relative}
  .card{position:absolute;left:150px;width:900px;height:500px;border-radius:28px;overflow:hidden}
  .card--back{top:40px;background:var(--navy)}
  .card--front{top:582px;background:var(--white)}

  .brand{position:absolute;display:flex;align-items:center;gap:16px}
  .brand__dot{width:44px;height:44px;border-radius:50%;background:var(--sky);flex:none}
  .brand__name{font-weight:600;font-size:40px;line-height:1.05;text-transform:uppercase;letter-spacing:1px}
  .card--back .brand{left:70px;top:200px}
  .card--back .brand__name{color:var(--white)}
  .card--front .brand{left:70px;top:90px}
  .card--front .brand__name{color:var(--navy)}

  .divider{position:absolute;left:520px;top:70px;width:3px;height:360px;background:var(--orange)}
  .services{position:absolute;left:560px;top:62px;list-style:none}
  .services li{display:flex;align-items:center;gap:12px;color:var(--white);font-size:19px;font-weight:400;letter-spacing:.8px;text-transform:uppercase;line-height:31px}
  .services svg{width:20px;height:20px;flex:none}

  .wave{position:absolute;left:0;top:0;width:900px;height:500px}
  .contact{position:absolute;right:60px;top:300px;text-align:right}
  .contact__name{font-weight:600;font-size:46px;color:var(--sky);text-transform:uppercase;letter-spacing:1px;line-height:1}
  .contact__title{font-weight:400;font-size:24px;color:var(--orange);text-transform:uppercase;letter-spacing:1px;margin-top:4px}
  .contact__lines{list-style:none;margin-top:12px}
  .contact__lines li{display:flex;justify-content:flex-end;align-items:center;gap:12px;color:var(--white);font-size:21px;letter-spacing:.6px;text-transform:uppercase;line-height:34px}
  .contact__lines svg{width:20px;height:20px;flex:none}
</style>
</head>
<body>

<section class="card card--back">
  <div class="brand">
    <span class="brand__dot"></span>
    <span class="brand__name">Tidewell<br>Pool Service</span>
  </div>
  <div class="divider"></div>
  <ul class="services">
    <li><svg viewBox="0 0 20 20"><circle cx="10" cy="10" r="10" fill="#22b0e6"/><path d="M5.5 10.5l3 3 6-6" stroke="#fff" stroke-width="2.2" fill="none"/></svg>Weekly pool maintenance</li>
    <li><svg viewBox="0 0 20 20"><circle cx="10" cy="10" r="10" fill="#22b0e6"/><path d="M5.5 10.5l3 3 6-6" stroke="#fff" stroke-width="2.2" fill="none"/></svg>Pool opening &amp; closing</li>
    <li><svg viewBox="0 0 20 20"><circle cx="10" cy="10" r="10" fill="#22b0e6"/><path d="M5.5 10.5l3 3 6-6" stroke="#fff" stroke-width="2.2" fill="none"/></svg>Equipment servicing</li>
    <li><svg viewBox="0 0 20 20"><circle cx="10" cy="10" r="10" fill="#22b0e6"/><path d="M5.5 10.5l3 3 6-6" stroke="#fff" stroke-width="2.2" fill="none"/></svg>Equipment installation</li>
    <li><svg viewBox="0 0 20 20"><circle cx="10" cy="10" r="10" fill="#22b0e6"/><path d="M5.5 10.5l3 3 6-6" stroke="#fff" stroke-width="2.2" fill="none"/></svg>Structural pool repair</li>
    <li><svg viewBox="0 0 20 20"><circle cx="10" cy="10" r="10" fill="#22b0e6"/><path d="M5.5 10.5l3 3 6-6" stroke="#fff" stroke-width="2.2" fill="none"/></svg>Plumbing updates &amp; upgrades</li>
    <li><svg viewBox="0 0 20 20"><circle cx="10" cy="10" r="10" fill="#22b0e6"/><path d="M5.5 10.5l3 3 6-6" stroke="#fff" stroke-width="2.2" fill="none"/></svg>Coping replacement &amp; removal</li>
    <li><svg viewBox="0 0 20 20"><circle cx="10" cy="10" r="10" fill="#22b0e6"/><path d="M5.5 10.5l3 3 6-6" stroke="#fff" stroke-width="2.2" fill="none"/></svg>Tile replacement &amp; removal</li>
    <li><svg viewBox="0 0 20 20"><circle cx="10" cy="10" r="10" fill="#22b0e6"/><path d="M5.5 10.5l3 3 6-6" stroke="#fff" stroke-width="2.2" fill="none"/></svg>Interior resurfacing/replastering</li>
    <li><svg viewBox="0 0 20 20"><circle cx="10" cy="10" r="10" fill="#22b0e6"/><path d="M5.5 10.5l3 3 6-6" stroke="#fff" stroke-width="2.2" fill="none"/></svg>Filter system equipment upgrades</li>
    <li><svg viewBox="0 0 20 20"><circle cx="10" cy="10" r="10" fill="#22b0e6"/><path d="M5.5 10.5l3 3 6-6" stroke="#fff" stroke-width="2.2" fill="none"/></svg>Decking removal &amp; renovation</li>
    <li><svg viewBox="0 0 20 20"><circle cx="10" cy="10" r="10" fill="#22b0e6"/><path d="M5.5 10.5l3 3 6-6" stroke="#fff" stroke-width="2.2" fill="none"/></svg>Commercial pool services</li>
  </ul>
</section>

<section class="card card--front">
  <svg class="wave" viewBox="0 0 900 500" aria-hidden="true">
    <path d="M0 228 C 170 330, 360 320, 560 262 S 820 208, 900 232 L900 500 L0 500 Z" fill="#e8682a"/>
    <path d="M0 246 C 170 350, 360 340, 560 278 S 820 222, 900 246 L900 500 L0 500 Z" fill="#22b0e6"/>
    <path d="M0 266 C 170 368, 370 356, 570 296 S 830 244, 900 272 L900 500 L0 500 Z" fill="#1f2d66"/>
  </svg>
  <div class="brand">
    <span class="brand__dot"></span>
    <span class="brand__name">Tidewell<br>Pool Service</span>
  </div>
  <div class="contact">
    <p class="contact__name">Dorian Pelkin</p>
    <p class="contact__title">Owner</p>
    <ul class="contact__lines">
      <li>(401) 582-7160<svg viewBox="0 0 20 20"><path d="M4 2l4 1 1 4-2 1.5c1 2.2 2.5 3.7 4.5 4.5L13 11l4 1 1 4-2 2C9 18 2 11 2 4z" fill="#22b0e6"/></svg></li>
      <li>Dorian@tidewellnx.com<svg viewBox="0 0 20 20"><rect x="1" y="4" width="18" height="12" rx="1.5" fill="#22b0e6"/><path d="M1.5 5l8.5 6 8.5-6" stroke="#1f2d66" stroke-width="1.6" fill="none"/></svg></li>
      <li>tidewellnx.com<svg viewBox="0 0 20 20"><circle cx="10" cy="10" r="9" fill="#22b0e6"/><path d="M1 10h18M10 1c-4 4-4 14 0 18M10 1c4 4 4 14 0 18" stroke="#1f2d66" stroke-width="1.4" fill="none"/></svg></li>
    </ul>
  </div>
</section>

</body>
</html>
```